The logo name is "Harbor Skin". The name of the product will be "Cutaneous Comfort". This product is specifically formulated for amputees. Therefore under the product name it should state "for amputees". The catch phrase will be "Experience Harbor find Calmness"
These are the things we need on the label:
Logo, product name, "for amputees", "Experience Harbor find Calmness", Safe, Effective, Directions: spray on problem areas, no need to dry off. harborskin.example, Made in Canada, 500ml.
The MOST IMPORTANT and therefore the most prominent thing on this lable will be the LOGO! The second most prominent thing will be the word "Comfort" We want to keep it very plain, very simple, very unclutered. Keep in mind that this lable will be placed on a white bottle or have a white back ground. The 500ml white PE bottle with trigger sprayer will have a tear drop label. See attached die line (S-294).
We want to stay with the colours that goes with the colour scheme of the logo. See attached logo. Soft colours. We do not want a picture! We would like the lable to be classy and rich.
Updates
The logo name is "Harbor Skin". The name of the product will be "Cutaneous Comfort". This product is specificlly formulated for amputees. Therefore under the product name it should state "for amputees". The catch phrase will be "Experience Harbor find Calmness"
Logo, product name, "for amputees", catch phrase "Experience Harbor find Calmness", Clean, Safe, Effective, Directions: spray on problem areas, no need to dry off. Also Harbor Skin Corpation, harborskin.example, Made in Canada, 500ml.
We want to stay with the colour scheme of the logo. See attached logo. Soft colours. We do not want a picture! We would like the lable to be classy and rich.
This is the offical directive that came from the governing panal of this lable. This panal it not know where it wanted to take this lable that would represent this line until they review all of your submissions, thank you for all your talented hard work. But now it is clear it is time to regroup and hit this objective.
Project Deadline Extended
Reason: New restrictions on lable wording for this product.
Target Market(s)
Amputees and Parents of.
Industry/Entity Type
Product
Requirements
Must have
- Final product to be in a pdf or an illustrator file

```html
<!DOCTYPE html>
<html lang="en">
<head>
<meta charset="utf-8">
<title>Harbor Skin – Cutaneous Comfort Label</title>
<link href="https://fonts.googleapis.com/css2?family=Questrial&display=swap" rel="stylesheet">
<style>
  :root {
    --page: #ffffff;
    --label-light: #a9b0b1;
    --label-dark: #7a8283;
    --mint: #8ef7b2;
    --mist: #e4f3f5;
    --ink-light: #f4f6f6;
    --brand-green: #17491c;
    --accent-orange: #f5a41c;
  }
  html, body {
    margin: 0;
    padding: 0;
    width: 1200px;
    height: 900px;
    overflow: hidden;
    background: var(--page);
    font-family: "Questrial", sans-serif;
  }
  .canvas {
    position: relative;
    width: 1200px;
    height: 900px;
  }
  .label-shape {
    position: absolute;
    inset: 0;
  }
  .label-text {
    position: absolute;
    margin: 0;
    color: var(--ink-light);
    white-space: nowrap;
    line-height: 1;
  }
  .volume { left: 483px; top: 180px; font-size: 31px; }
  .origin { left: 486px; top: 214px; font-size: 13px; }
  .claims { left: 461px; top: 371px; font-size: 20px; }
  .brand {
    position: absolute;
    left: 458px;
    top: 412px;
    display: flex;
    align-items: center;
    gap: 14px;
  }
  .brand-mark {
    width: 62px;
    height: 62px;
    background: var(--mint);
  }
  .brand-name {
    font-size: 40px;
    color: var(--brand-green);
    line-height: 1;
  }
  .product-line { left: 460px; top: 518px; font-size: 21px; }
  .product-name { left: 456px; top: 550px; font-size: 66px; color: var(--accent-orange); }
  .audience { left: 460px; top: 625px; font-size: 20px; }
  .directions { left: 458px; top: 657px; font-size: 14px; line-height: 1.25; white-space: normal; width: 240px; }
  .directions strong { display: block; font-size: 13px; font-weight: 700; }
  .tagline { left: 460px; top: 777px; font-size: 19px; }
  .website { left: 461px; top: 802px; font-size: 13px; color: var(--accent-orange); }
</style>
</head>
<body>
<main class="canvas">
  <svg class="label-shape" viewBox="0 0 1200 900" width="1200" height="900" aria-hidden="false">
    <defs>
      <radialGradient id="label-fill" cx="0.62" cy="0.42" r="0.7">
        <stop offset="0" stop-color="var(--label-light)"/>
        <stop offset="1" stop-color="var(--label-dark)"/>
      </radialGradient>
      <radialGradient id="grass-fill" cx="0.5" cy="0.5" r="0.5">
        <stop offset="0" stop-color="#f7a21a"/>
        <stop offset="1" stop-color="#f7a21a" stop-opacity="0"/>
      </radialGradient>
      <clipPath id="teardrop">
        <path d="M540 40 C560 36 580 45 600 70 C760 250 880 450 864 680 C857 760 842 812 818 833 L455 833 C440 833 431 820 429 800 C405 600 430 300 510 62 C518 46 528 40 540 40 Z"/>
      </clipPath>
    </defs>
    <path class="label-body" fill="url(#label-fill)" d="M540 40 C560 36 580 45 600 70 C760 250 880 450 864 680 C857 760 842 812 818 833 L455 833 C440 833 431 820 429 800 C405 600 430 300 510 62 C518 46 528 40 540 40 Z"/>
    <g clip-path="url(#teardrop)">
      <path class="band-mist" fill="var(--mist)" d="M500 94 C650 140 770 270 826 430 C846 520 836 620 808 690 C796 560 768 430 724 350 C664 230 592 160 497 114 Z"/>
      <path class="band-mint" fill="var(--mint)" d="M497 110 C602 150 702 252 758 400 C790 500 792 650 808 840 L768 840 C768 700 758 560 728 452 C688 302 600 172 497 128 Z"/>
      <ellipse class="grass-accent" role="img" aria-label="Decorative orange grass sprig" cx="756" cy="400" rx="26" ry="56" fill="url(#grass-fill)"/>
    </g>
  </svg>

  <p class="label-text volume">500ml</p>
  <p class="label-text origin">made in Canada</p>
  <p class="label-text claims">Safe . Effective</p>

  <div class="brand">
    <span class="brand-mark"></span>
    <span class="brand-name">Harbor Skin</span>
  </div>

  <p class="label-text product-line">Cutaneous</p>
  <h1 class="label-text product-name" style="font-weight:400">Comfort</h1>
  <p class="label-text audience">For Amputees</p>
  <p class="label-text directions"><strong>Directions</strong>Spray on problem areas,<br>no need to dry off.</p>

  <p class="label-text tagline">Experience Harbor, Find Calmness</p>
  <p class="label-text website">harborskin.example</p>
</main>
</body>
</html>
```